Web landing page design

- Create a Web Design (Uncoded - PSD layout only)

We need a single web page design to promote our service. This page will
acts as a landing page for users and also be utilized in social media
advertising. Please provide us with a cutting edge design. I have attached
a link for what the company is about. In essence we are a photo checking
service which reviews photos for retailers, hotels abd car dealerships to
check everything is good after a service has been performed. Whether it be
a new promotion, cleaning or just checking prices. I am looking for a
design to say that we do many photos and at a very cost effective price
(team based in Mexico)

Link: https://slidevault.example/view/qTr8nWx2LpZk4mHcYdJs/
*Deadline*
5 days
*Updates*

- The Start Here box needs to look like this:

-Start Here (heading)
-A box for email addresses to be entered
-Then a check box with "Yes, I have read and agree to the Privacy Policy
and agree to receive email marketing from Plumora88'
-A submit button

All of this information needs to be in one box please. And please feel
free to contact me if you have any questions about this.

*Target Market(s)*
Retail business, Merchandising companies, Rental property owners, Car
dealers
Updates

Please can you submit entries. I am just looking for a tidy to a presentation already created. Just needs design touches.

Target Market(s)

Ability for audience to understand concept quickly
Benefits to why to use the product stand out
Technology driven approach

Industry/Entity Type

Retail

Number of Pages Required

1 page

Colors
0792cd

Requirements
Must have
• Clean and modern design

```html
<!DOCTYPE html>
<html lang="en">
<head>
<meta charset="utf-8">
<title>Plumora88 – Photo verification for retail</title>
<link href="https://fonts.googleapis.com/css2?family=Open+Sans:wght@400;600;700&family=Roboto+Condensed:wght@400&display=swap" rel="stylesheet">
<style>
  :root {
    --brand-blue: #0792cd;
    --band-blue: #1170ad;
    --band-blue-dark: #0c5f98;
    --hero-dark: #3b4450;
    --hero-mid: #6b6e72;
    --hero-warm: #8a7260;
    --panel-bg: #ebebed;
    --ink: #1d1d1f;
    --white: #ffffff;
    --footer-bg: #000000;
  }
  * { box-sizing: border-box; margin: 0; padding: 0; }
  html, body { width: 1200px; height: 837px; overflow: hidden; }
  body { font-family: "Open Sans", Arial, sans-serif; color: var(--white); position: relative; background: var(--footer-bg); }

  .hero { position: absolute; left: 0; top: 0; width: 1200px; height: 593px; overflow: hidden; }
  .hero-photo {
    position: absolute; inset: 0;
    background:
      radial-gradient(ellipse at 50% 45%, rgba(170,140,120,0.55) 0%, rgba(0,0,0,0) 45%),
      radial-gradient(ellipse at 80% 85%, rgba(140,110,80,0.5) 0%, rgba(0,0,0,0) 50%),
      linear-gradient(135deg, var(--hero-dark) 0%, var(--hero-mid) 45%, var(--hero-warm) 75%, #4b3f36 100%);
  }
  .hero-photo::after { content: ""; position: absolute; inset: 0; background: rgba(30,35,45,0.35); }

  .brand { position: absolute; left: 93px; top: 22px; width: 110px; text-align: center; }
  .brand-dot { display: block; width: 36px; height: 36px; border-radius: 50%; background: var(--brand-blue); margin: 0 auto 4px 34px; }
  .brand-name { display: block; font-size: 30px; font-weight: 600; letter-spacing: 1px; line-height: 1; text-align: left; }

  .main-nav { position: absolute; top: 55px; left: 0; width: 1200px; }
  .main-nav a { position: absolute; color: var(--white); text-decoration: none; font-size: 16.5px; white-space: nowrap; }
  .main-nav a.is-active { font-weight: 700; }

  .hero-title {
    position: absolute; left: 91px; top: 253px;
    font-family: "Roboto Condensed", "Arial Narrow", sans-serif;
    font-size: 42px; line-height: 54px; font-weight: 400;
  }
  .slider-controls { position: absolute; left: 91px; top: 374px; display: flex; gap: 3px; }
  .slider-controls span { width: 22px; height: 22px; border-radius: 50%; background: #222; border: 1px solid #777; display: flex; align-items: center; justify-content: center; }

  .signup-panel { position: absolute; left: 743px; top: 190px; width: 368px; height: 244px; background: var(--panel-bg); border-radius: 3px; color: var(--ink); }
  .signup-title { text-align: center; font-size: 35px; font-weight: 600; margin-top: 17px; line-height: 44px; }
  .email-field { position: absolute; left: 27px; top: 75px; width: 313px; height: 52px; border: 1px solid #555; background: #f2f2f2; font: 400 17px "Open Sans", sans-serif; color: var(--ink); padding-left: 19px; }
  .email-field::placeholder { color: var(--ink); opacity: 1; }
  .consent { position: absolute; left: 27px; top: 139px; display: flex; gap: 8px; }
  .consent-box { width: 23px; height: 23px; border: 1px solid #7a8790; background: var(--white); flex: none; display: flex; align-items: center; justify-content: center; }
  .consent-text { font-size: 11.6px; line-height: 22px; letter-spacing: -0.25px; margin-top: -4px; color: #333; white-space: nowrap; }
  .submit-button { position: absolute; left: 120px; top: 187px; width: 108px; height: 35px; background: var(--brand-blue); color: var(--white); border: none; border-radius: 2px; font: 400 21px "Open Sans", sans-serif; }

  .stats-band { position: absolute; left: 0; top: 593px; width: 1200px; height: 174px; background: linear-gradient(120deg, var(--band-blue) 0%, var(--band-blue-dark) 50%, var(--band-blue) 100%); overflow: hidden; }
  .stat { position: absolute; width: 200px; margin-left: -100px; text-align: center; }
  .stat-value { font-size: 47px; font-weight: 600; line-height: 1; }
  .stat-label { font-size: 15px; line-height: 18px; margin-top: 6px; }

  .site-footer { position: absolute; left: 0; top: 767px; width: 1200px; height: 70px; background: var(--footer-bg); }
  .copyright { position: absolute; left: 0; width: 1153px; top: 26px; text-align: center; font-size: 15px; }
</style>
</head>
<body>
  <header class="hero">
    <div class="hero-photo" role="img" aria-label="Photo of hands using a smartphone over a tablet on a desk"></div>

    <div class="brand">
      <span class="brand-dot"></span>
      <span class="brand-name">plumora</span>
    </div>

    <nav class="main-nav">
      <a class="is-active" style="left:528px">Home</a>
      <a style="left:623px">About Us</a>
      <a style="left:738px">Results</a>
      <a style="left:832px">How</a>
      <a style="left:907px">Free Trial</a>
      <a style="left:1022px">Contact us</a>
    </nav>

    <h1 class="hero-title">Transform retail execution<br>with a simple photo</h1>
    <div class="slider-controls">
      <span><svg width="10" height="10" viewBox="0 0 10 10"><path d="M6.5 1.5 3 5l3.5 3.5" fill="none" stroke="#fff" stroke-width="1.8"/></svg></span>
      <span><svg width="10" height="10" viewBox="0 0 10 10"><path d="M3.5 1.5 7 5 3.5 8.5" fill="none" stroke="#fff" stroke-width="1.8"/></svg></span>
    </div>

    <form class="signup-panel">
      <h2 class="signup-title">Start Here</h2>
      <input class="email-field" type="email" placeholder="Email id" aria-label="Email id">
      <label class="consent">
        <span class="consent-box"><svg width="17" height="14" viewBox="0 0 17 14"><path d="M1.5 7.5 6 12 15.5 2" fill="none" stroke="#0792cd" stroke-width="3"/></svg></span>
        <span class="consent-text">Yes, I have read and agree to the Privacy Policy<br>and agree to receive email marketing from Plumora88</span>
      </label>
      <button class="submit-button" type="button">submit</button>
    </form>
  </header>

  <section class="stats-band">
    <div class="stat" style="left:250px;top:40px"><div class="stat-value">2.2m</div><div class="stat-label">Photos reviewed<br>last year</div></div>
    <div class="stat" style="left:484px;top:30px"><div class="stat-value">5p</div><div class="stat-label">From per<br>photo reviewed</div></div>
    <div class="stat" style="left:718px;top:40px"><div class="stat-value">97.2%</div><div class="stat-label">Average compliance</div></div>
    <div class="stat" style="left:952px;top:40px"><div class="stat-value">3-8%</div><div class="stat-label">Sales increase</div></div>
  </section>

  <footer class="site-footer">
    <p class="copyright">Copyright © 2018&nbsp; All Rights Reserved</p>
  </footer>
</body>
</html>
```